Fitness Equipment & Service

I want to make the card eye catching and fun. We are called Corvane Motion Limited and we are based in Wales. We sell, install and service all types of fitness equipment from Skipping ropes, right through the Dumbbells, Kettle bells and Barbells through to state of the art Treadmills, Running Machines and Strength Equipment. We also design and install changing room furniture and lockers.

TYPOGRAPHY
We would like to use Futrura. Futura has an appearance of efficiency and forwardness. The typeface is derived
from simple geometric forms (near-perfect circles, triangles and squares) and is based on strokes of
near-even weight, which are low in contrast. This is most visible in the almost perfectly round stroke of
the o, which is nonetheless slightly ovoid.
The lowercase has tall ascenders, which rise above the cap line. The uppercase
characters present proportions similar to those of classical Roman capitals.

TYPOGRAPHIC CONSIDERATIONS
No Strike though
No Horizontal Scaling
No Drop Shadows
No Effects
Never use less than 120% Leading

OUR CORPORATE COLOURS
BRAND GUIDELINES
We were thinking that our primary colour palette consists of the Acid Green (Pantone 382) and Process Black.

We work closely with tquarly Ltd and would like to include their name on the card somewhere. I have attached images of the other brands that we work with as an idea or the small icons I have included that illustrate what we do?. I have very kindly been given permission to use any of the images off the files that I have included below, so I hope these help. I will include these below. I would be open to suggestions if it made the card more striking Can you do it?
Updates

Hi All, Just wanted to add a few thoughts but you are the guys with the creative visions (thats why are here) We are based in Wales, UK and we would be open to lots of different ideas on a theme but must be eye catching, Bold and FUN. If you can or think that the Welsh or any dragon could be put in there then go for it (its not a must have) We have also added some ideas for colour but again its over to you!! GO FOR IT ! Thanks and look forward to your visions! Owen

Hi All, Just thought I would sen through the contact details that need to be on the card. (if you want to play around with icons instead of the wording twitter, Facebook, go for it): Corvane Motion Limited Owen Pritchard Managing Director Mob: +44 (0)7582 913 406 e-mail: sales@corvanemotion.co.uk Web: Corvanemotion.co.uk twitter: @motionLetterbin Facebook: Corvane Motion Limited

```html
<!DOCTYPE html>
<html lang="en">
<head>
<meta charset="utf-8">
<title>Corvane Motion Limited – Business Card</title>
<link rel="stylesheet" href="https://fonts.googleapis.com/css2?family=Jost:wght@400;500;700&display=swap">
<style>
  :root {
    --navy: #1a1150;
    --navy-deep: #120b3d;
    --gold: #b8953c;
    --gold-light: #c9a64a;
    --white: #ffffff;
    --paper: #f7f7f7;
    --stage: #e6e4e0;
    --tile-1: #1f64ad;
    --tile-2: #2b7fd0;
    --tile-3: #38b4e8;
    --tile-4: #7f9cb5;
    --tile-5: #bcc8d3;
    --tile-6: #134b86;
    --tile-7: #0f3766;
  }
  * { box-sizing: border-box; margin: 0; padding: 0; }
  html, body { width: 1200px; height: 892px; overflow: hidden; }
  body {
    background: var(--stage);
    font-family: "Jost", sans-serif;
    position: relative;
  }
  .card {
    position: absolute;
    left: 250px;
    width: 700px;
    height: 400px;
    border-radius: 4px;
    overflow: hidden;
    box-shadow: 0 4px 14px rgba(0,0,0,0.18);
  }

  /* ---------- Back card ---------- */
  .card--back { top: 30px; background: var(--tile-1); }
  .tile-grid {
    position: absolute; inset: 0;
    display: grid;
    grid-template-columns: repeat(7, 1fr);
    grid-template-rows: repeat(4, 1fr);
  }
  .tile-grid span:nth-child(1)  { background: var(--tile-1); }
  .tile-grid span:nth-child(2)  { background: var(--tile-3); }
  .tile-grid span:nth-child(3)  { background: var(--tile-6); }
  .tile-grid span:nth-child(4)  { background: var(--tile-2); }
  .tile-grid span:nth-child(5)  { background: var(--tile-1); }
  .tile-grid span:nth-child(6)  { background: var(--tile-6); }
  .tile-grid span:nth-child(7)  { background: var(--tile-2); }
  .tile-grid span:nth-child(8)  { background: var(--tile-2); }
  .tile-grid span:nth-child(9)  { background: var(--tile-4); }
  .tile-grid span:nth-child(10) { background: var(--tile-7); }
  .tile-grid span:nth-child(11) { background: var(--tile-6); }
  .tile-grid span:nth-child(12) { background: var(--tile-1); }
  .tile-grid span:nth-child(13) { background: var(--tile-7); }
  .tile-grid span:nth-child(14) { background: var(--tile-6); }
  .tile-grid span:nth-child(15) { background: var(--tile-7); }
  .tile-grid span:nth-child(16) { background: var(--tile-1); }
  .tile-grid span:nth-child(17) { background: var(--tile-5); }
  .tile-grid span:nth-child(18) { background: var(--tile-6); }
  .tile-grid span:nth-child(19) { background: var(--tile-2); }
  .tile-grid span:nth-child(20) { background: var(--tile-7); }
  .tile-grid span:nth-child(21) { background: var(--tile-1); }
  .tile-grid span:nth-child(22) { background: var(--tile-1); }
  .tile-grid span:nth-child(23) { background: var(--tile-6); }
  .tile-grid span:nth-child(24) { background: var(--tile-7); }
  .tile-grid span:nth-child(25) { background: var(--tile-4); }
  .tile-grid span:nth-child(26) { background: var(--tile-1); }
  .tile-grid span:nth-child(27) { background: var(--tile-6); }
  .tile-grid span:nth-child(28) { background: var(--tile-7); }
  .back-name {
    position: absolute;
    left: 0; right: 0; top: 150px;
    text-align: center;
    color: var(--white);
    font-weight: 700;
    font-size: 52px;
    line-height: 1.2;
  }

  /* ---------- Front card ---------- */
  .card--front { top: 462px; background: var(--paper); }
  .front-shape { position: absolute; inset: 0; }
  .brand {
    position: absolute;
    left: 40px; top: 40px;
    display: flex; align-items: center; gap: 16px;
  }
  .brand-dot {
    width: 64px; height: 64px; border-radius: 50%;
    background: var(--navy);
  }
  .brand-name {
    color: var(--navy);
    font-weight: 500;
    font-size: 24px;
    line-height: 1.2;
  }
  .person {
    position: absolute;
    right: 40px; top: 150px;
    text-align: right;
  }
  .person-name {
    color: var(--gold-light);
    font-weight: 500;
    font-size: 38px;
    line-height: 1.2;
  }
  .person-role {
    color: var(--white);
    font-size: 18px;
    line-height: 1.3;
  }
  .contacts {
    position: absolute;
    right: 40px; top: 238px;
    list-style: none;
  }
  .contacts li {
    display: flex; justify-content: flex-end; align-items: center; gap: 12px;
    color: var(--white);
    font-size: 16px;
    line-height: 1.3;
    height: 28px;
  }
  .contact-mark {
    width: 14px; height: 14px;
    background: var(--gold);
    flex: none;
  }
</style>
</head>
<body>

  <section class="card card--back" aria-label="Card back">
    <div class="tile-grid" role="img" aria-label="Grid of blue tiles with fitness icons: treadmill, exercise bike, kettlebell, skipping rope, nutrition, scales and boxing gloves">
      <span></span><span></span><span></span><span></span><span></span><span></span><span></span>
      <span></span><span></span><span></span><span></span><span></span><span></span><span></span>
      <span></span><span></span><span></span><span></span><span></span><span></span><span></span>
      <span></span><span></span><span></span><span></span><span></span><span></span><span></span>
    </div>
    <p class="back-name">Corvane Motion Limited</p>
  </section>

  <section class="card card--front" aria-label="Card front">
    <svg class="front-shape" width="700" height="400" viewBox="0 0 700 400" aria-hidden="true">
      <path d="M0 190 Q 330 200 700 110 L700 400 L0 400 Z" fill="var(--gold)"/>
      <path d="M0 200 Q 330 210 700 122 L700 400 L0 400 Z" fill="var(--navy)"/>
    </svg>

    <div class="brand">
      <span class="brand-dot"></span>
      <span class="brand-name">Corvane Motion Limited</span>
    </div>

    <div class="person">
      <p class="person-name">Owen Pritchard</p>
      <p class="person-role">Managing Director</p>
    </div>

    <ul class="contacts">
      <li>@motionLetterbin<span class="contact-mark"></span></li>
      <li>+44 (0)7582 913 406<span class="contact-mark"></span></li>
      <li>Corvanemotion.co.uk<span class="contact-mark"></span></li>
      <li>Corvane Motion Limited<span class="contact-mark"></span></li>
      <li>sales@corvanemotion.co.uk<span class="contact-mark"></span></li>
    </ul>
  </section>

</body>
</html>
```